Post Disaster Temporary Housing Literature Review poster

Wanting a poster design for two Emergency Management conferences we have coming up. The information to be included in the poster is capturing the purpose, findings and recommendations from a post disaster temporary housing literature review looking at “What should government consider in order to improve planning and decision making for accommodation needs after a disaster, and to support people’s transition to stable housing?”
I’d like to enhance the visual appeal through including relevant images or graphic. I am also open to reducing the text if needed.
The government group I work with focuses on the social and human side of disaster recovery so keen for any images to reflect the human aspect and not focus solely on disasters or housing.
Government and NGO's

```html
<!DOCTYPE html>
<html lang="en">
<head>
<meta charset="utf-8">
<title>Post Disaster Temporary Housing – Literature Review</title>
<link href="https://fonts.googleapis.com/css2?family=Montserrat:wght@400;800;900&family=Lato:wght@400&display=swap" rel="stylesheet">
<style>
  :root {
    --brand-blue: #1b9ad0;
    --brand-blue-dark: #1586bd;
    --ink: #111111;
    --ink-soft: #2a2a2a;
    --paper: #ffffff;
  }
  * { margin: 0; padding: 0; box-sizing: border-box; }
  html, body { width: 848px; height: 1200px; overflow: hidden; background: var(--paper); }
  .poster { position: relative; width: 848px; height: 1200px; overflow: hidden; background: var(--paper); font-family: 'Lato', sans-serif; color: var(--ink); }

  .brand { position: absolute; z-index: 2; left: 22px; top: 29px; display: flex; align-items: center; gap: 12px; }
  .brand-mark { width: 100px; height: 100px; border-radius: 50%; border: 5px solid var(--brand-blue); flex: none; }
  .brand-name { font-family: 'Montserrat', sans-serif; font-weight: 400; color: var(--ink-soft); font-size: 15px; line-height: 20px; white-space: nowrap; }
  .brand-name span { display: block; }
  .brand-name .brand-country { font-size: 12px; letter-spacing: 2px; margin-top: 5px; }

  .hero-photo { position: absolute; z-index: 1; left: 293px; top: 0; width: 555px; height: 302px; }

  .question { position: absolute; left: 35px; top: 159px; font-family: 'Montserrat', sans-serif; font-weight: 900; font-size: 18.6px; line-height: 22.6px; color: var(--ink); }
  .intro { position: absolute; left: 35px; top: 314px; width: 790px; font-size: 19.4px; line-height: 24.6px; color: var(--ink); }

  .pillars { position: absolute; left: 0; top: 439px; width: 848px; height: 233px; background: var(--brand-blue); }
  .pillar { position: absolute; top: 36px; color: var(--paper); }
  .pillar-icon { width: 68px; height: 68px; border-radius: 50%; background: var(--paper); display: flex; align-items: center; justify-content: center; }
  .pillar-title { margin-top: 23px; font-family: 'Montserrat', sans-serif; font-weight: 400; font-size: 20.6px; line-height: 24.6px; letter-spacing: 0.4px; }
  .pillar--practice { left: 35px; }
  .pillar--practice .pillar-title { padding-left: 4px; }
  .pillar--temporary { left: 298px; }
  .pillar--framework { left: 570px; }

  .couple-photo { position: absolute; left: 0; top: 672px; width: 425px; height: 337px; }

  .recommendations { position: absolute; left: 457px; top: 705px; }
  .recommendations h2 { font-family: 'Montserrat', sans-serif; font-weight: 900; font-size: 23px; letter-spacing: 0.3px; color: var(--ink); }
  .recommendations ol { list-style: none; margin-top: 17px; }
  .recommendations li { font-size: 18px; line-height: 22.6px; color: var(--ink); }
  .recommendations li b { font-weight: 400; display: inline-block; width: 24px; }

  .next-steps { position: absolute; left: 0; top: 1008px; width: 848px; height: 192px; background: var(--brand-blue); }
  .next-steps-photo { position: absolute; right: 0; top: 0; width: 340px; height: 192px; background: linear-gradient(90deg, var(--brand-blue) 0%, rgba(27,154,208,0.4) 25%, #c7b9a3 55%, #d98a5e 80%, #e8c7a4 100%); }
  .next-steps h2 { position: absolute; left: 34px; top: 28px; font-family: 'Montserrat', sans-serif; font-weight: 900; font-size: 23px; color: var(--paper); }
  .next-steps p { position: absolute; left: 34px; top: 68px; width: 485px; font-size: 16.8px; line-height: 16.5px; color: var(--paper); }
</style>
</head>
<body>
<main class="poster">

  <svg class="hero-photo" viewBox="0 0 555 302" role="img" aria-label="Photo: smiling family of four standing in front of their suburban home">
    <defs>
      <linearGradient id="heroTones" x1="0" y1="0" x2="0" y2="1">
        <stop offset="0" stop-color="#a9d2ec"/>
        <stop offset="0.45" stop-color="#e2d6c4"/>
        <stop offset="0.75" stop-color="#c99a86"/>
        <stop offset="1" stop-color="#7fa65a"/>
      </linearGradient>
    </defs>
    <path d="M0,0 C18,150 200,302 385,302 C470,302 535,255 555,222 L555,0 Z" fill="var(--brand-blue)"/>
    <path d="M30,0 C55,140 220,290 388,292 C470,292 535,242 555,208 L555,0 Z" fill="url(#heroTones)"/>
  </svg>

  <div class="brand">
    <div class="brand-mark"></div>
    <div class="brand-name">
      <span>Community Recovery</span>
      <span>Advisory Council</span>
      <span class="brand-country">AUSTRALIA</span>
    </div>
  </div>

  <h1 class="question">What should government<br>consider in order to improve<br>planning and decision making for<br>accommodation needs after a<br>disaster, and to support people’s<br>transition to stable housing?</h1>

  <p class="intro">The full report was commissioned by the Community Recovery Advisory Council (CRAC) and undertaken by Helena Marsden and Peter Alcott through the Southern Coast Institute of Technology (SCIT). The findings and recommendations may be utilised by stakeholders.</p>

  <section class="pillars">
    <div class="pillar pillar--practice">
      <div class="pillar-icon">
        <svg width="44" height="44" viewBox="0 0 44 44" aria-hidden="true">
          <path d="M22 5 L40 21 Q41 24 38 24 L36 24 L36 39 L27 39 L27 29 L17 29 L17 39 L8 39 L8 24 L6 24 Q3 24 4 21 Z" fill="var(--brand-blue)" stroke="var(--brand-blue)" stroke-width="2" stroke-linejoin="round"/>
        </svg>
      </div>
      <div class="pillar-title">Leading practice in<br>disaster&nbsp; housing<br>recovery</div>
    </div>
    <div class="pillar pillar--temporary">
      <div class="pillar-icon">
        <svg width="44" height="44" viewBox="0 0 44 44" aria-hidden="true">
          <g fill="none" stroke="var(--brand-blue)" stroke-width="3.5" stroke-linecap="round" stroke-linejoin="round">
            <path d="M22 24 V6 M17 11 L22 5 L27 11"/>
            <path d="M20 22 Q14 16 7 16 M10 12 L5 16 L10 20"/>
            <path d="M24 22 Q30 16 37 16 M34 12 L39 16 L34 20"/>
          </g>
          <circle cx="22" cy="32" r="6" fill="none" stroke="var(--brand-blue)" stroke-width="5" stroke-dasharray="3 2"/>
          <circle cx="22" cy="32" r="2" fill="var(--brand-blue)"/>
        </svg>
      </div>
      <div class="pillar-title">Innovative<br>approaches to<br>temporary housing</div>
    </div>
    <div class="pillar pillar--framework">
      <div class="pillar-icon">
        <svg width="46" height="46" viewBox="0 0 46 46" aria-hidden="true">
          <circle cx="23" cy="20" r="6" fill="var(--brand-blue)"/>
          <path d="M12 40 Q12 28 23 28 Q34 28 34 40 Z" fill="var(--brand-blue)"/>
          <g fill="none" stroke="var(--brand-blue)" stroke-width="2.5" stroke-linecap="round" stroke-linejoin="round">
            <path d="M23 11 V3 M20 6 L23 3 L26 6"/>
            <path d="M14 20 H4 M7 17 L4 20 L7 23"/>
            <path d="M32 20 H42 M39 17 L42 20 L39 23"/>
            <path d="M16 13 L10 7 M10 11 V7 H14"/>
            <path d="M30 13 L36 7 M32 7 H36 V11"/>
          </g>
        </svg>
      </div>
      <div class="pillar-title">A decision-making<br>framework for resilient<br>housing recovery</div>
    </div>
  </section>

  <svg class="couple-photo" viewBox="0 0 425 337" role="img" aria-label="Photo: couple seen from behind, arm in arm, looking at a modern house">
    <defs>
      <linearGradient id="coupleTones" x1="0" y1="0" x2="1" y2="1">
        <stop offset="0" stop-color="#b9d9ef"/>
        <stop offset="0.4" stop-color="#e9ecef"/>
        <stop offset="0.75" stop-color="#3b5b9a"/>
        <stop offset="1" stop-color="#8c8f86"/>
      </linearGradient>
    </defs>
    <polygon points="0,0 389,0 421,337 0,337" fill="url(#coupleTones)"/>
  </svg>

  <section class="recommendations">
    <h2>RECOMMENDATIONS</h2>
    <ol>
      <li><b>1.</b>Terminology</li>
      <li><b>2.</b>Principles</li>
      <li><b>3.</b>National Principles</li>
      <li><b>4.</b>Guidelines</li>
      <li><b>5.</b>Capacity Building</li>
      <li><b>6.</b>Funding</li>
      <li><b>7.</b>Further Research</li>
      <li><b>8.</b>Pilot Project</li>
      <li><b>9.</b>Decision Making Framework</li>
      <li><b>10.</b>&nbsp;&nbsp;Capturing Learnings</li>
    </ol>
  </section>

  <section class="next-steps">
    <div class="next-steps-photo" role="img" aria-label="Photo: open hand holding a small model house"></div>
    <h2>NEXT STEPS</h2>
    <p>The Community Recovery Advisory Council is partnering with Hazard Resilience Research Australia to analyse previous post-disaster temporary housing assistance and support mechanisms used in Australia. The project aims to provide national guidance on the design and implementation of temporary housing from the research and resources developed.</p>
  </section>

</main>
</body>
</html>
```